Van Sign Writing for Electrical & Security Systems Compay

We are an Electrical, Intruder Alarm / CCTV and Automation company. We would like a design to have our van Sign Written. The van is a 2021 Velmont ostrel. We DON'T want to completely wrap it, just work with the colour of the van and the logo and wording provided. Although we are open to some unique designs to complement the logo and wording. Pictures of the van front, side and back have been provided along with the logo.

Please use fake placeholders for the Phone Number Email Address and Web Address, these will be provided later.

The Servies that need to be displayed are:

Electrical
Intruder Alarms & CCTV
Access Control
EV Chargers
Home Automation
Fire Alarms
Fire Protection

The social media Icons that need to be displayed are:
Chatterbox
Pixelane
Yappline
Quillpost
Blinkreel
There needs to be space under these icons for a web address. The exact van colour is VELMONT PAINT KPW GRIS URBAN. The image also attached of colour.

Target Market(s)

Electrical
Intruder Alarms & CCTV
Access Control
EV Chargers
Home Automation
Fire Alarms
Fire Protection

Requirements
Must have
• As per Description
Nice to have
• Unique design to compliment text, logo and colours
Should not have
• Full wrap

```html
<!DOCTYPE html>
<html lang="en">
<head>
<meta charset="utf-8">
<title>Kelvane van sign writing</title>
<link rel="stylesheet" href="https://fonts.googleapis.com/css2?family=Montserrat:wght@600;700;800&family=Nunito:wght@800&display=swap">
<style>
:root{
  --teal:#7fcfdb;
  --van-teal:#9ccfd6;
  --dark:#2b2d30;
  --dark-2:#46494d;
  --silver:#d9d9db;
  --white:#ffffff;
  --bg:#e4e4e6;
}
*{margin:0;padding:0;box-sizing:border-box}
html,body{width:1196px;height:1200px;overflow:hidden;background:var(--bg)}
.canvas{position:relative;width:1196px;height:1200px;background:linear-gradient(#dcdcde,#eeeeef 50%,#dcdcde)}
.side{position:absolute;left:0;width:1196px;height:600px}
.side--left{top:0}
.side--right{top:600px}
.side-graphic{position:absolute;left:0;top:0;width:1196px;height:600px}
.side--right .side-graphic{transform:scaleX(-1)}
.brand-name{position:absolute;width:310px;font:800 64px/1 "Montserrat",sans-serif;color:var(--teal);letter-spacing:-2px;white-space:nowrap}
.side--right .brand-name{text-align:right}
.brand-mark{position:absolute;width:112px;height:112px;border:9px solid var(--teal);border-radius:50%}
.tagline{position:absolute;font:700 20px/1 "Montserrat",sans-serif;color:var(--white);letter-spacing:.18em;white-space:nowrap}
.phone-band{position:absolute;height:50px;width:410px;background:var(--teal)}
.phone{position:absolute;font:700 44px/50px "Montserrat",sans-serif;color:var(--white);letter-spacing:1px;white-space:nowrap}
.email{position:absolute;font:600 16px/1 "Montserrat",sans-serif;color:var(--white);letter-spacing:.14em;white-space:nowrap}
.web{position:absolute;font:700 25px/1 "Montserrat",sans-serif;color:var(--white);letter-spacing:.3em;white-space:nowrap}
.socials{position:absolute;display:flex;gap:10px;list-style:none}
.socials li{display:flex;align-items:center;gap:4px;font:600 11px/1 "Montserrat",sans-serif;color:var(--white)}
.socials li::before{content:"";width:10px;height:10px;border:1.5px solid var(--white);border-radius:50%}
.services{position:absolute;list-style:none}
.services li{font:800 16.5px/20.6px "Nunito",sans-serif;color:var(--white);display:flex;align-items:center;gap:9px}
.services li::before{content:"";width:7px;height:7px;border-radius:50%;background:var(--white)}
</style>
</head>
<body>
<main class="canvas">

  <section class="side side--left">
    <svg class="side-graphic" viewBox="0 0 1196 600" aria-hidden="true">
      <defs>
        <linearGradient id="darkFadeA" x1="0" y1="0" x2="0" y2="1">
          <stop offset="0" stop-color="#3c3f43"/><stop offset=".5" stop-color="#2b2d30"/><stop offset="1" stop-color="#1f2022"/>
        </linearGradient>
        <linearGradient id="silverA" x1="0" y1="0" x2="1" y2="1">
          <stop offset="0" stop-color="#f4f4f5"/><stop offset=".5" stop-color="#b9babd"/><stop offset="1" stop-color="#ececee"/>
        </linearGradient>
      </defs>
      <rect x="20" y="80" width="1156" height="410" rx="40" fill="var(--van-teal)"/>
      <path d="M528 80 C490 250 560 420 720 490 L760 490 C600 420 530 250 568 80 Z" fill="url(#silverA)"/>
      <path d="M568 80 C530 250 600 420 760 490 L1136 490 Q1176 490 1176 450 L1176 120 Q1176 80 1136 80 Z" fill="url(#darkFadeA)"/>
    </svg>
    <span class="brand-mark" style="left:632px;top:112px"></span>
    <h1 class="brand-name" style="left:766px;top:142px">KELVANE</h1>
    <p class="tagline" style="left:768px;top:210px">GET CONNECTED</p>
    <div class="phone-band" style="left:706px;top:234px"></div>
    <p class="phone" style="left:758px;top:234px">123 456 7890</p>
    <p class="email" style="left:746px;top:294px">kelvanegetconnected@mailbox.com</p>
    <p class="web" style="left:746px;top:316px">www.kelvane.com</p>
    <ul class="socials" style="left:652px;top:372px">
      <li>Yappline</li><li>Chatterbox</li><li>Pixelane</li><li>Blinkreel</li><li>Quillpost</li>
    </ul>
    <ul class="services" style="left:306px;top:320px">
      <li>Electrical</li><li>Intruder Alarms &amp; CCTV</li><li>Access Control</li><li>EV Chargers</li><li>Home Automation</li><li>Fire Alarms</li><li>Fire Protection</li>
    </ul>
  </section>

  <section class="side side--right">
    <svg class="side-graphic" viewBox="0 0 1196 600" aria-hidden="true">
      <defs>
        <linearGradient id="darkFadeB" x1="0" y1="0" x2="0" y2="1">
          <stop offset="0" stop-color="#3c3f43"/><stop offset=".5" stop-color="#2b2d30"/><stop offset="1" stop-color="#1f2022"/>
        </linearGradient>
        <linearGradient id="silverB" x1="0" y1="0" x2="1" y2="1">
          <stop offset="0" stop-color="#f4f4f5"/><stop offset=".5" stop-color="#b9babd"/><stop offset="1" stop-color="#ececee"/>
        </linearGradient>
      </defs>
      <rect x="20" y="80" width="1156" height="410" rx="40" fill="var(--van-teal)"/>
      <path d="M480 80 C440 250 510 420 680 490 L720 490 C560 420 490 250 520 80 Z" fill="url(#silverB)"/>
      <path d="M520 80 C490 250 560 420 720 490 L1136 490 Q1176 490 1176 450 L1176 120 Q1176 80 1136 80 Z" fill="url(#darkFadeB)"/>
    </svg>
    <h2 class="brand-name" style="left:116px;top:142px">KELVANE</h2>
    <span class="brand-mark" style="left:446px;top:112px"></span>
    <p class="tagline" style="left:200px;top:210px">GET CONNECTED</p>
    <div class="phone-band" style="left:78px;top:234px"></div>
    <p class="phone" style="left:122px;top:234px">123 456 7890</p>
    <p class="email" style="left:120px;top:294px">kelvanegetconnected@mailbox.com</p>
    <p class="web" style="left:120px;top:316px">www.kelvane.com</p>
    <ul class="socials" style="left:206px;top:372px">
      <li>Yappline</li><li>Chatterbox</li><li>Pixelane</li><li>Blinkreel</li><li>Quillpost</li>
    </ul>
    <ul class="services" style="left:700px;top:320px">
      <li>Electrical</li><li>Intruder Alarms &amp; CCTV</li><li>Access Control</li><li>EV Chargers</li><li>Home Automation</li><li>Fire Alarms</li><li>Fire Protection</li>
    </ul>
  </section>

</main>
</body>
</html>
```